Flyer Design Project for psychologist

I need an A4 flyer designed for a new psychology practice I am setting up called Harbour Bloom. The focus is to cater for the mental health and well-being of mums throughout their life stages, to help them live their best life whilst providing support and guidance in their journey through Motherhood.
The flyer will be used to promote the main services we provide and will echo the look and feel of website (www.harbourbloom.com.au) and logo design. Images/photos can be downloaded off the Harbour Bloom website homepage slider or on "Our Services" page.
Corporate colours
Colours:
Bright green: Pantone 376
Bright green as CMYK: c: 45.2% m: 0% y: 100% k: 0%
Logo text large grey: 70% black
Logo text strapline: 75% black
Tree: 80% black
Fonts:
Logo 'Harbour Bloom': Verdana
Logo 'Counselling & coaching services for mums': Gill Sans Light
Updates
OMG you are all awesome!!!! Will be very very hard decision :-(
Target Market(s)
Mothers - all life stages wanting support counselling
Industry/Entity Type
Mental Health
Look and feel
Each slider illustrates characteristics of the customer's brand and the style your logo design should communicate.

```html
<!DOCTYPE html>
<html lang="en">
<head>
<meta charset="utf-8">
<title>Harbour Bloom – Counselling and Coaching for Mums</title>
<link href="https://fonts.googleapis.com/css2?family=Noto+Sans:wght@700;800&family=Lato:wght@300;400&display=swap" rel="stylesheet">
<style>
  :root {
    --green: #7ed320;
    --grey-logo: #4d4d4d;
    --grey-head: #333333;
    --grey-body: #595959;
    --white: #ffffff;
    --sky: #8cc0ea;
    --sky-light: #cfe4f6;
    --warm: #e9b69f;
  }
  * { margin: 0; padding: 0; box-sizing: border-box; }
  html, body { width: 849px; height: 1200px; overflow: hidden; background: var(--white); }
  .flyer { position: relative; width: 849px; height: 1200px; overflow: hidden; background: var(--white); }

  .hero-photo {
    position: absolute; left: 0; top: 0; width: 849px; height: 453px;
    background: linear-gradient(100deg, var(--sky-light) 0%, var(--sky) 45%, var(--warm) 100%);
  }
  .hero-veil {
    position: absolute; left: 0; top: 100px; width: 640px; height: 290px;
    background: linear-gradient(90deg, rgba(255,255,255,.6) 60%, rgba(255,255,255,0));
  }

  .brand { position: absolute; left: 50px; top: 116px; display: flex; align-items: center; gap: 14px; }
  .brand-name { font-family: "Noto Sans", sans-serif; font-weight: 700; font-size: 42px; line-height: 52px; color: var(--grey-logo); }
  .brand-dot { width: 18px; height: 18px; border-radius: 50%; background: var(--green); }

  .headline {
    position: absolute; left: 52px; top: 254px; width: 600px;
    font-family: "Noto Sans", sans-serif; font-weight: 800; font-size: 31px; line-height: 41px;
    letter-spacing: 0.6px; color: var(--grey-head);
  }

  .band { position: absolute; left: 0; width: 849px; height: 25px; background: var(--green); }
  .band--top { top: 453px; }
  .band--middle { top: 1012px; height: 26px; }
  .band--bottom { top: 1174px; height: 26px; }

  .intro {
    position: absolute; left: 50px; top: 500px; width: 745px;
    font-family: "Lato", sans-serif; font-weight: 300; font-size: 18.6px; line-height: 25px;
    color: var(--grey-body);
  }
  .intro p + p { margin-top: 25px; }

  .services {
    position: absolute; left: 60px; top: 770px; width: 760px;
    display: grid; grid-template-columns: 363px 397px;
    font-family: "Lato", sans-serif; font-weight: 300; font-size: 18.6px; line-height: 25.5px;
    color: var(--grey-body); list-style: none;
  }
  .services li { padding-left: 18px; position: relative; white-space: nowrap; }
  .services li::before { content: "•"; position: absolute; left: 0; }

  .contact {
    position: absolute; left: 52px; top: 958px;
    font-family: "Noto Sans", sans-serif; font-weight: 800; font-size: 18.5px; line-height: 24px;
    letter-spacing: 0.4px; color: var(--grey-body); white-space: nowrap;
  }

  .strip { position: absolute; top: 1038px; height: 136px; }
  .strip--mother-baby { left: 0; width: 262px; background: linear-gradient(90deg, #f2d6c2, #f7e9de); }
  .strip--puzzle { left: 264px; width: 320px; background: linear-gradient(90deg, #f3ece6, #f6f3f0); }
  .strip--group { left: 586px; width: 263px; background: linear-gradient(180deg, #7fa356, #8c6a55); }
</style>
</head>
<body>
<div class="flyer">
  <div class="hero-photo" role="img" aria-label="Photo of a smiling mother hugging her daughter outdoors against a blue sky with soft coloured balloons"></div>
  <div class="hero-veil"></div>

  <div class="brand">
    <span class="brand-name">Harbour Bloom</span>
    <span class="brand-dot"></span>
  </div>

  <h1 class="headline">Live your best with<br>Harbour Bloom Counselling<br>and Coaching for Mums</h1>

  <div class="band band--top"></div>

  <div class="intro">
    <p>Harbour Bloom provides counselling and coaching services especially for mums. Our main focus is to help you effectively deal with the daily issues that you may face that impacts on your mental health and wellbeing whilst providing support and guidance in your journey throughout Motherhood.</p>
    <p>We help mums to uncover their strengths, set purposeful goals, develop the skills, ability and confidence that they need to be happier and lead meaningful and flourishing lives.</p>
    <p>We can provide counselling and coaching for:</p>
  </div>

  <ul class="services">
    <li>Non-Directive Pregnancy Support</li>
    <li>Motherhood Stress and Anger</li>
    <li>Antenatal Depression</li>
    <li>Surviving and Thriving Through a Breakup</li>
    <li>Preparing for Baby</li>
    <li>Work/Family Balance</li>
    <li>Postnatal Depression</li>
    <li>Increasing Happiness</li>
    <li>Anxiety</li>
    <li>Finding Yourself in Motherhood</li>
  </ul>

  <p class="contact">Call (02) 9000 4821 or visit our website: www.harbourbloom.com.au</p>

  <div class="band band--middle"></div>

  <div class="strip strip--mother-baby" role="img" aria-label="Close-up photo of a mother and baby touching noses"></div>
  <div class="strip strip--puzzle" role="img" aria-label="Photo of cupped hands holding colourful puzzle pieces"></div>
  <div class="strip strip--group" role="img" aria-label="Photo of a group of mums with their babies in a garden"></div>

  <div class="band band--bottom"></div>
</div>
</body>
</html>
```